Redesign website for small print company

Vindurgata is a small printing company in Iceland mainly servicing Students, schools, etc. We are also doing all kind of other jobs, like business cards, book printing, brochure printing etc. We are also selling books online.
Our website is: www.vindurgata.is
What we are looking for is:
- Web Design (Uncoded - PSD layout only)
- Mobile friendly design, using our current color scheme: Red, green, yellow and light gray.
- Clean simple design
- Simple, light and easy to use.
- More menu Items/drop down
Industry/Entity Type
Digital Printing
Number of Pages Required
5+ page
Requirements
Must have
- Easy navigation
- Designed for mobile
- Current color scheme (see logo)
Nice to have
- Icon based products

```html
<!DOCTYPE html>
<html lang="en">
<head>
<meta charset="utf-8">
<title>Vindurgata — Full Service Printing</title>
<link rel="stylesheet" href="https://fonts.googleapis.com/css2?family=Roboto:ital,wght@0,400;0,500;0,700;1,400;1,500&display=swap">
<style>
:root{
  --red:#e8312f;
  --green:#1c6b3c;
  --yellow:#f5d20f;
  --light:#efefef;
  --light2:#e6e6e6;
  --dark:#231f20;
  --ink:#222;
  --muted:#555;
  --white:#fff;
}
*{box-sizing:border-box;margin:0;padding:0}
html,body{width:1200px;height:3103px;overflow:hidden}
body{font-family:'Roboto',sans-serif;color:var(--ink);background:var(--white);position:relative}
.abs{position:absolute}

/* top bar */
.topbar{position:absolute;left:0;top:0;width:1200px;height:38px;background:var(--light);font-size:12px;color:#333}
.topbar .item{position:absolute;top:11px;display:flex;align-items:center;gap:12px}
.topbar svg{width:14px;height:14px}
.lang{position:absolute;left:931px;top:0;width:124px;height:38px;background:#d9d9d9;display:flex;align-items:center;justify-content:center;gap:8px;font-size:12px}

/* nav */
.nav{position:absolute;left:0;top:38px;width:1200px;height:74px;background:var(--white)}
.brand{position:absolute;left:140px;top:20px;display:flex;align-items:center;gap:10px;font-weight:700;font-size:27px;color:var(--ink);letter-spacing:.5px}
.brand .sq{width:30px;height:30px;background:var(--red)}
.menu{position:absolute;top:24px;font-size:12px;font-weight:500;color:var(--ink)}
.menu.active{color:var(--red)}
.dropdown{position:absolute;left:670px;top:87px;width:178px;height:149px;background:var(--white);box-shadow:0 2px 8px rgba(0,0,0,.2);font-size:12px;z-index:3}
.dropdown div{height:36px;line-height:36px;padding-left:14px;border-bottom:1px solid #eee;margin:0 8px 0 0}

/* hero */
.hero{position:absolute;left:0;top:112px;width:1200px;height:529px;background:radial-gradient(ellipse at 50% 35%,#4a4446 0%,#2a2627 55%,#1b1819 100%)}
.hero-art{position:absolute;left:340px;top:100px;width:520px;height:300px;border-radius:4px;background:linear-gradient(135deg,#8e8a86 0%,#c9b9a8 40%,#6e6a70 100%);opacity:.55}
.hero h1{position:absolute;left:0;top:385px;width:1200px;text-align:center;color:var(--white);font-weight:500;font-size:33px;letter-spacing:.5px}
.hero h1 span{color:var(--red);border-bottom:3px solid var(--red);padding-bottom:2px}

/* section titles */
.sec-title{position:absolute;left:0;width:1200px;text-align:center;font-size:33px;font-weight:500;color:var(--ink)}
.sec-title::first-letter{color:var(--red)}
.sec-title.light{color:var(--white)}
.divider{position:absolute;left:478px;width:244px;height:16px}
.divider::before,.divider::after{content:"";position:absolute;top:7px;width:104px;height:2px;background:#8a8a8a}
.divider::before{left:0}.divider::after{right:0}
.divider span{position:absolute;left:114px;top:0;width:16px;height:16px;background:var(--yellow);border:2px solid var(--red)}

/* about */
.about{position:absolute;left:0;top:641px;width:1200px;height:476px;background:var(--white)}
.about-text{position:absolute;left:140px;top:166px;width:605px;font-size:11.5px;line-height:16px;color:#333}
.about-text h3{font-size:16px;font-weight:500;color:var(--ink);margin-bottom:8px}
.about-text h3::first-letter{color:var(--red)}
.about-text p{margin-bottom:17px}
.about-mark{position:absolute;left:883px;top:180px;width:174px;height:224px;background:var(--light);display:flex;flex-direction:column;align-items:center;justify-content:center;gap:14px;box-shadow:0 2px 6px rgba(0,0,0,.12)}
.about-mark .sq{width:58px;height:58px;background:var(--green)}
.about-mark .name{font-size:20px;font-weight:700;color:var(--ink)}

/* products */
.products{position:absolute;left:0;top:1117px;width:1200px;height:656px;background:var(--light)}
.card{position:absolute;width:281px;height:193px;background:#f5f5f5;text-align:center}
.card.featured{background:var(--white);box-shadow:0 3px 10px rgba(0,0,0,.18)}
.card .ico{position:absolute;left:100px;top:32px;width:80px;height:80px;border-radius:50%;border:2px solid #d6d6d6;background:var(--white);display:flex;align-items:center;justify-content:center}
.card .ico svg{width:40px;height:40px;fill:none;stroke:var(--green);stroke-width:2}
.card.featured .ico svg{stroke:var(--red)}
.card .label{position:absolute;left:0;top:128px;width:100%;font-size:17px;font-weight:500;color:var(--ink)}
.card.featured .label{color:var(--red)}

/* why */
.why{position:absolute;left:0;top:1773px;width:1200px;height:451px;background:linear-gradient(180deg,#2b2a30 0%,#34323a 50%,#262428 100%)}
.feat{position:absolute;width:430px}
.feat .circ{position:absolute;left:0;top:0;width:74px;height:74px;border-radius:50%;background:var(--white);display:flex;align-items:center;justify-content:center}
.feat .circ svg{width:36px;height:36px;fill:var(--green)}
.feat h4{position:absolute;left:89px;top:0;font-size:15px;font-weight:500;color:var(--white)}
.feat p{position:absolute;left:89px;top:21px;width:338px;font-size:11.5px;line-height:16px;color:#ddd}

/* testimonials */
.testi{position:absolute;left:0;top:2224px;width:1200px;height:387px;background:var(--white)}
.quote{position:absolute;left:165px;top:156px;width:880px;text-align:center;font-style:italic;font-size:12px;line-height:20px;color:#444}
.author{position:absolute;left:0;top:236px;width:1200px;text-align:center;color:var(--red);font-style:italic;font-weight:500;font-size:14px}
.arrow{position:absolute;top:211px;width:46px;height:65px;display:flex;align-items:center;justify-content:center}
.arrow svg{width:20px;height:36px;fill:none;stroke-width:2}
.avatar{position:absolute;left:571px;top:267px;width:58px;height:60px;background:linear-gradient(160deg,#7b6c5e,#3d3a36);border:2px solid #ddd}
.dots{position:absolute;left:573px;top:352px;display:flex;gap:12px}
.dots span{width:9px;height:9px;border-radius:50%;background:#ddd}
.dots span:first-child{background:var(--green)}

/* newsletter */
.news{position:absolute;left:0;top:2611px;width:1200px;height:87px;background:var(--light2)}
.news .env{position:absolute;left:141px;top:21px;width:45px;height:45px;border-radius:50%;border:2px solid var(--ink);display:flex;align-items:center;justify-content:center}
.news h5{position:absolute;left:199px;top:30px;font-size:21px;font-weight:400;color:var(--ink)}
.news .input{position:absolute;left:513px;top:27px;width:377px;height:31px;background:var(--white);font-size:10px;color:#888;padding:10px}
.news .btn{position:absolute;left:904px;top:27px;width:153px;height:31px;background:var(--red);color:var(--white);font-size:15px;font-weight:500;display:flex;align-items:center;justify-content:center}

/* footer */
.footer{position:absolute;left:0;top:2698px;width:1200px;height:356px;background:var(--dark);color:var(--white)}
.footer h6{position:absolute;top:62px;font-size:17px;font-weight:400}
.field{position:absolute;left:141px;width:240px;background:var(--white);font-size:11px;color:#888;padding:8px}
.send{position:absolute;left:141px;top:257px;width:85px;height:27px;background:var(--red);font-size:12px;font-weight:500;display:flex;align-items:center;justify-content:center}
.map{position:absolute;left:457px;top:97px;width:294px;height:187px;background:linear-gradient(135deg,#cfe3f1 0%,#e8eee4 45%,#d4e6cf 100%)}
.contact{position:absolute;left:826px;font-size:12px;line-height:16px;display:flex;gap:10px}
.contact svg{width:13px;height:15px;fill:var(--red);flex:none;margin-top:1px}
.social{position:absolute;left:826px;top:208px;width:16px;height:16px;background:#cfcfcf}

.bottom{position:absolute;left:0;top:3054px;width:1200px;height:49px;background:var(--red);color:var(--white);font-size:11px}
.bottom .copy{position:absolute;left:141px;top:18px}
.pay{position:absolute;top:13px;width:38px;height:24px;border-radius:3px;background:var(--white)}
</style>
</head>
<body>

<header class="topbar">
  <div class="item" style="left:145px"><svg viewBox="0 0 24 24"><path fill="#1c6b3c" d="M6.6 10.8a15 15 0 006.6 6.6l2.2-2.2a1 1 0 011-.25 11.4 11.4 0 003.6.6 1 1 0 011 1V20a1 1 0 01-1 1A17 17 0 013 4a1 1 0 011-1h3.5a1 1 0 011 1c0 1.25.2 2.45.6 3.6a1 1 0 01-.25 1z"/></svg>555 4120</div>
  <div class="item" style="left:383px"><svg viewBox="0 0 24 24"><path fill="#1c6b3c" d="M2 5h20v14H2z"/><path fill="none" stroke="#fff" stroke-width="1.6" d="M2 6l10 7 10-7"/></svg>verk@vindurgata.is</div>
  <div class="item" style="left:672px"><svg viewBox="0 0 24 24"><circle cx="12" cy="12" r="9" fill="none" stroke="#1c6b3c" stroke-width="2.5"/><path d="M12 7v5l3 2" fill="none" stroke="#1c6b3c" stroke-width="2"/></svg>Mon - Fri: 9-17</div>
  <div class="lang">Language <svg width="10" height="6" viewBox="0 0 10 6"><path d="M0 0h10L5 6z" fill="#222"/></svg></div>
</header>

<nav class="nav">
  <div class="brand"><span class="sq"></span>VINDURGATA</div>
  <span class="menu" style="left:505px">HOME</span>
  <span class="menu" style="left:575px">ABOUT US</span>
  <span class="menu active" style="left:668px">SERVICES &#8964;</span>
  <span class="menu" style="left:776px">PRODUCTS</span>
  <span class="menu" style="left:875px">JOB SUBMIT</span>
  <span class="menu" style="left:983px">CONTACT US</span>
</nav>
<div class="dropdown">
  <div>Bookprinting</div>
  <div>Better Finances</div>
  <div>Photocopying</div>
  <div style="border:none">Spiral-bound books</div>
</div>

<section class="hero">
  <div class="hero-art" role="img" aria-label="Stack of printed magazines, books and business cards on a desk"></div>
  <h1>FULL <span>SERVICE PRINTING</span> WITH A SMAILE.</h1>
</section>

<section class="about">
  <h2 class="sec-title" style="top:57px">ABOUT US</h2>
  <div class="divider" style="top:112px"><span></span></div>
  <div class="about-text">
    <h3>Welcome to University</h3>
    <p>University education is a company located in the campus, which has specialized in the service of school staff, as well as providing general public printing.</p>
    <p>Higher education publishes seminars and first-class textbooks for courses, prints theses for lesson, as well as working on an unprecedented number of smaller pieces for students, teachers and organizations. These include brochures, reports, questionnaires, business cards, books, OCR scanning and more.</p>
    <p>Higher education is a tailored print shop, The Leaf is the official eco-label of the Nordic countries, which has created a foothold in this country and is known among consumers.</p>
    <p>University education is located at the corner of Mosagata and Hlidargata. (walked into Hlidargötumegin)</p>
  </div>
  <div class="about-mark"><span class="sq"></span><span class="name">Vindurgata</span></div>
</section>

<section class="products">
  <h2 class="sec-title" style="top:66px">OUR PRODUCTS</h2>
  <div class="divider" style="top:122px"><span></span></div>

  <div class="card featured" style="left:141px;top:162px">
    <div class="ico"><svg viewBox="0 0 40 40"><path d="M10 4h15l7 7v25H10z"/><path d="M15 16h12M15 21h12M15 26h8"/></svg></div>
    <div class="label">ESSAYS</div>
  </div>
  <div class="card" style="left:459px;top:162px">
    <div class="ico"><svg viewBox="0 0 40 40"><rect x="4" y="9" width="32" height="22" rx="2"/><circle cx="13" cy="18" r="3"/><path d="M9 26c1-3 7-3 8 0M21 16h10M21 21h10M21 26h7"/></svg></div>
    <div class="label">BUSINESS CARDS</div>
  </div>
  <div class="card" style="left:778px;top:162px">
    <div class="ico"><svg viewBox="0 0 40 40"><path d="M4 9l10-3 12 3 10-3v25l-10 3-12-3-10 3z"/><path d="M14 6v25M26 9v25M8 15h3M17 15h6M29 15h4M8 21h3M17 21h6M29 21h4"/></svg></div>
    <div class="label">LEAFLETS</div>
  </div>
  <div class="card" style="left:141px;top:391px">
    <div class="ico"><svg viewBox="0 0 40 40"><rect x="11" y="4" width="20" height="30" rx="1"/><path d="M8 8v29h20M15 11h12M15 16h12M15 21h12M15 26h8"/></svg></div>
    <div class="label">BOOK PRINTING</div>
  </div>
  <div class="card" style="left:459px;top:391px">
    <div class="ico"><svg viewBox="0 0 40 40"><rect x="9" y="4" width="22" height="32"/><path d="M13 9h14v12H13zM13 21l5-6 4 4 2-2 3 4M13 26h14M13 30h10"/></svg></div>
    <div class="label">POSTERS</div>
  </div>
  <div class="card" style="left:778px;top:391px">
    <div class="ico"><svg viewBox="0 0 40 40"><path d="M9 6h22v28H12a3 3 0 01-3-3z"/><path d="M9 31a3 3 0 013-3h19M15 6v22M19 12h8"/></svg></div>
    <div class="label">TEXTBOOKS</div>
  </div>
</section>

<section class="why" role="img" aria-label="Dark backdrop of fanned colour swatch cards">
  <h2 class="sec-title light" style="top:62px">WHY CHOOSE US ?</h2>
  <div class="divider" style="top:117px"><span></span></div>

  <div class="feat" style="left:141px;top:184px">
    <div class="circ"><svg viewBox="0 0 36 36"><path d="M6 11l12-6 12 6v14l-12 6-12-6z"/><path d="M6 11l12 6 12-6M18 17v14" stroke="#fff" stroke-width="1.5" fill="none"/></svg></div>
    <h4>Over 200k Orders Completed</h4>
    <p>It is a long established fact that a reader will be distracted by the readable content of a page when looking at its layout.</p>
  </div>
  <div class="feat" style="left:641px;top:184px">
    <div class="circ"><svg viewBox="0 0 36 36"><circle cx="18" cy="10" r="5"/><circle cx="8" cy="14" r="4"/><circle cx="28" cy="14" r="4"/><path d="M9 30c0-7 4-11 9-11s9 4 9 11zM1 28c0-5 3-8 7-8 1 0 2 0 3 1-2 2-3 4-3 7zM35 28c0-5-3-8-7-8-1 0-2 0-3 1 2 2 3 4 3 7z"/></svg></div>
    <h4>Great Customer Service</h4>
    <p>It is a long established fact that a reader will be distracted by the readable content of a page when looking at its layout.</p>
  </div>
  <div class="feat" style="left:141px;top:302px">
    <div class="circ"><svg viewBox="0 0 36 36"><path d="M10 6h16l7 9-15 17L3 15z"/><path d="M3 15h30M12 6l-2 9 8 17 8-17-2-9" stroke="#fff" stroke-width="1.3" fill="none"/></svg></div>
    <h4>Superior Quality and Value</h4>
    <p>It is a long established fact that a reader will be distracted by the readable content of a page when looking at its layout.</p>
  </div>
  <div class="feat" style="left:641px;top:302px">
    <div class="circ"><svg viewBox="0 0 36 36"><circle cx="21" cy="18" r="12"/><path d="M21 11v7l5 3" stroke="#fff" stroke-width="2" fill="none"/><path d="M2 13h6M0 18h6M2 23h6" stroke="#1c6b3c" stroke-width="2"/></svg></div>
    <h4>Fast Turnaround</h4>
    <p>It is a long established fact that a reader will be distracted by the readable content of a page when looking at its layout.</p>
  </div>
</section>

<section class="testi">
  <h2 class="sec-title" style="top:60px">CLIENT TESTIMONIALS</h2>
  <div class="divider" style="top:115px"><span></span></div>
  <p class="quote">Lorem ipsum dolor sit amet, consectetur adipiscing elit, sed do eiusmod tempor incididunt ut labore et dolore magna aliqua. Ut enim &nbsp;veniam, quis nostrud exercitation ullamco laboris nisi ut aliquip ex ea commodo consequat. Duis aute irure dolor in reprehenderit in voluptate velit esse cillum dolore eu fugiat nulla pariatur. Excepteur sint occaecat cupidatat non proident, sunt in culpa qui officia .</p>
  <div class="author">- Sconsectetur adipiscing</div>
  <div class="arrow" style="left:75px;background:#e4e4e4"><svg viewBox="0 0 20 36"><path d="M17 2L3 18l14 16" stroke="#fff"/></svg></div>
  <div class="arrow" style="left:1080px;background:var(--green)"><svg viewBox="0 0 20 36"><path d="M3 2l14 16L3 34" stroke="#fff"/></svg></div>
  <div class="avatar" role="img" aria-label="Client portrait photo"></div>
  <div class="dots"><span></span><span></span><span></span></div>
</section>

<section class="news">
  <div class="env"><svg width="22" height="16" viewBox="0 0 22 16"><rect x="1" y="1" width="20" height="14" fill="none" stroke="#222" stroke-width="2"/><path d="M1 1l10 8 10-8" fill="none" stroke="#222" stroke-width="2"/></svg></div>
  <h5>SIGN UP FOR NEWSLETTER</h5>
  <div class="input">Enter your email here</div>
  <div class="btn">SUBSCRIBE</div>
</section>

<footer class="footer">
  <h6 style="left:141px">DROP US A LINE</h6>
  <h6 style="left:457px">LOCATION MAP</h6>
  <h6 style="left:826px">FIND US</h6>

  <div class="field" style="top:97px;height:29px">Name</div>
  <div class="field" style="top:137px;height:29px">Email</div>
  <div class="field" style="top:176px;height:68px">Message</div>
  <div class="send">SEND</div>

  <div class="map" role="img" aria-label="Street map showing the shop location"></div>

  <div class="contact" style="top:94px"><svg viewBox="0 0 13 15"><path d="M6.5 0A5 5 0 001.5 5c0 4 5 10 5 10s5-6 5-10a5 5 0 00-5-5zm0 7a2 2 0 110-4 2 2 0 010 4z"/></svg><span>48 Harbor Lane<br>Eastfield, Oregon 97201-4410</span></div>
  <div class="contact" style="top:143px"><svg viewBox="0 0 24 24"><path d="M6.6 10.8a15 15 0 006.6 6.6l2.2-2.2a1 1 0 011-.25 11.4 11.4 0 003.6.6 1 1 0 011 1V20a1 1 0 01-1 1A17 17 0 013 4a1 1 0 011-1h3.5a1 1 0 011 1c0 1.25.2 2.45.6 3.6a1 1 0 01-.25 1z"/></svg><span>555 4120</span></div>
  <div class="contact" style="top:174px"><svg viewBox="0 0 24 24"><path d="M2 5h20v14H2z"/></svg><span>verk@vindurgata.is</span></div>
  <div class="social"></div>
</footer>

<div class="bottom">
  <div class="copy">Copyright © 2018 Vindurgata. All Rights Reserved</div>
  <div class="pay" style="left:973px"></div>
  <div class="pay" style="left:1019px"></div>
</div>

</body>
</html>
```